Website Quibrel Outdoor

Hi I'm looking for a simple design for a new website. It's outdoor products mainly in category, Boat, Tarpaulin, Fishing, Golf. I have include image and text for 8 products + presentation etc. I want a simple and modern site + fast + Mobile. Wordpress. I'm going to sell through Tradovik so I don't need any WooCommerce but a buy button to Tradovik. I haven set up the Tradovik account yet. My logo i s grey and orange. My goal is to sell in Tradovik US and later EU.

```html
<!DOCTYPE html>
<html lang="en">
<head>
<meta charset="utf-8">
<title>Quibrel Outdoor</title>
<link rel="stylesheet" href="https://fonts.googleapis.com/css2?family=Montserrat:wght@400;500;600;700&family=Nunito:wght@700;800;900&family=Roboto:wght@400;500&display=swap">
<style>
:root{
  --orange:#f07f1e;
  --grey:#6d6e71;
  --dark:#333333;
  --darker:#262626;
  --ink:#222222;
  --text:#333333;
  --white:#ffffff;
  --head:"Montserrat",sans-serif;
  --round:"Nunito",sans-serif;
  --body:"Roboto",sans-serif;
}
*{box-sizing:border-box;margin:0;padding:0}
html,body{width:1200px;height:3601px;overflow:hidden;background:var(--white)}
body{position:relative;font-family:var(--body);color:var(--text)}
.abs{position:absolute}
.btn{position:absolute;display:flex;align-items:center;justify-content:center;border-radius:26px;font-family:var(--head);font-weight:500;color:var(--white);font-size:18px;text-decoration:none}
.btn-orange{background:var(--orange)}
.btn-dark{background:#2f2f2f}

/* header */
.site-header{position:absolute;left:0;top:0;width:1200px;height:143px;background:var(--white)}
.brand{position:absolute;left:75px;top:18px;display:flex;flex-direction:column;align-items:center;gap:8px;width:132px}
.brand-dot{width:46px;height:46px;border-radius:50%;background:#6d6e71}
.brand-name{font-family:var(--head);font-weight:700;font-size:22px;color:var(--orange);line-height:1;white-space:nowrap}
.nav a{position:absolute;top:49px;height:48px;display:flex;align-items:center;font-family:var(--head);font-size:16px;font-weight:500;color:var(--ink);text-decoration:none}
.nav .active{left:381px;width:110px;justify-content:center;background:var(--orange);color:var(--white);border-radius:24px}

/* hero */
.hero{position:absolute;left:0;top:143px;width:1200px;height:695px;background:linear-gradient(135deg,#5e6b4a 0%,#7e8f55 40%,#5a7a35 70%,#3f4a3a 100%)}
.hero-title{position:absolute;left:0;top:225px;width:1200px;text-align:center;font-family:var(--round);font-weight:900;font-size:84px;line-height:74px;color:var(--white)}
.hero .btn{left:511px;top:405px;width:178px;height:51px}
.dots{position:absolute;top:642px;left:555px;display:flex;gap:16px}
.dots span{width:10px;height:10px;border-radius:50%;background:var(--white)}
.dots span:first-child{background:var(--orange)}

/* category */
.section-title{position:absolute;font-family:var(--head);font-weight:500;color:var(--ink)}
.category-title{left:0;width:1200px;top:898px;text-align:center;font-size:42px}
.tile{position:absolute;width:512px;height:294px}
.tile .band{position:absolute;left:0;top:115px;width:512px;height:65px;background:rgba(240,127,30,.92);display:flex;align-items:center;justify-content:center;font-family:var(--round);font-weight:800;font-size:38px;color:var(--white)}

/* products */
.products{position:absolute;left:0;top:1673px;width:1200px;height:658px;background:var(--grey)}
.products-title{position:absolute;left:0;width:1200px;top:75px;display:flex;justify-content:center;align-items:center;gap:26px;font-family:var(--head);font-weight:500;font-size:42px;color:var(--white)}
.product-photo{position:absolute;left:75px;top:169px;width:512px;height:404px;background:linear-gradient(160deg,#3a3f44 0%,#7d848a 35%,#5f8f2e 70%,#4c7d24 100%)}
.product-photo .thumb{position:absolute;left:300px;top:205px;width:180px;height:180px;border-radius:50%;background:#f2f2f2;border:4px solid #fff}
.product-info{position:absolute;left:617px;top:166px;width:508px;color:var(--white)}
.product-info h3{font-family:var(--head);font-weight:600;font-size:30px;margin-bottom:12px}
.product-info p{font-size:14px;line-height:27.7px}

/* about + news */
.about-title{left:75px;top:2392px;font-size:42px}
.news-title{left:617px;top:2392px;font-size:42px}
.about-photo{position:absolute;left:75px;top:2460px;width:512px;height:273px;background:linear-gradient(120deg,#54603f 0%,#8a7a5c 40%,#d0672a 65%,#3f4a36 100%)}
.about-text{position:absolute;left:75px;top:2752px;width:500px;font-size:14px;line-height:27.7px;color:var(--text)}
.news-item{position:absolute;left:617px;width:515px;height:150px}
.news-item .pic{position:absolute;left:0;top:0;width:188px;height:145px}
.news-item h4{position:absolute;left:208px;top:0;width:300px;font-family:var(--head);font-weight:600;font-size:19.5px;line-height:27px;color:var(--orange)}
.news-item p{position:absolute;left:208px;top:58px;width:300px;font-size:13.5px;line-height:25px;color:var(--text)}

/* footer */
.site-footer{position:absolute;left:0;top:3058px;width:1200px;height:480px;background:var(--dark);color:var(--white)}
.foot-brand{position:absolute;left:75px;top:40px;display:flex;flex-direction:column;align-items:center;gap:6px;width:100px}
.foot-brand .brand-dot{width:36px;height:36px}
.foot-brand .brand-name{font-size:21px}
.foot-h{position:absolute;font-family:var(--head);font-weight:500;font-size:28px}
.newsletter-input{position:absolute;left:253px;top:82px;width:378px;height:53px;border-radius:27px;background:var(--white);color:#444;font-size:16px;display:flex;align-items:center;padding-left:22px}
.site-footer .signup{left:641px;top:82px;width:164px;height:53px;font-size:22px}
.social{position:absolute;left:884px;top:100px;width:242px;display:flex;justify-content:space-between;font-family:var(--head);font-size:10px;font-weight:600}
.divider{position:absolute;left:75px;top:162px;width:1050px;height:1px;background:#555}
.foot-col{position:absolute;top:212px}
.foot-col h5{font-family:var(--head);font-weight:500;font-size:21px;margin-bottom:12px}
.foot-col li{list-style:none;font-family:var(--head);font-size:14.5px;line-height:31.5px}
.shop-word{font-family:var(--head);font-weight:700;font-size:46px;color:var(--white);margin-top:6px}
.copyright{position:absolute;left:0;top:3538px;width:1200px;height:63px;background:var(--darker);color:#ddd;font-size:13px;display:flex;align-items:center;justify-content:center}
</style>
</head>
<body>

<header class="site-header">
  <div class="brand"><span class="brand-dot"></span><span class="brand-name">Quibrel Outdoor</span></div>
  <nav class="nav">
    <a class="active" href="#">Home</a>
    <a href="#" style="left:505px">About Us</a>
    <a href="#" style="left:629px">Categories</a>
    <a href="#" style="left:764px">Products</a>
    <a href="#" style="left:884px">Latest News</a>
    <a href="#" style="left:1032px">Contact Us</a>
  </nav>
</header>

<section class="hero" role="img" aria-label="Golf bag on a cart on grass, gloved hand wiping a club with a towel">
  <h1 class="hero-title">Welcome<br>Quibrel Outdoor</h1>
  <a class="btn btn-orange" href="#">Buy Now</a>
  <div class="dots"><span></span><span></span><span></span><span></span></div>
</section>

<h2 class="section-title category-title">Category</h2>
<div class="tile" style="left:75px;top:984px;background:linear-gradient(135deg,#9a9ea2,#e2e2e2 60%,#b9bcbe)" role="img" aria-label="Boat console with steering wheel"><div class="band">Boat</div></div>
<div class="tile" style="left:616px;top:984px;background:linear-gradient(135deg,#5a6b80,#c9d8ea 50%,#2355b5)" role="img" aria-label="Blue tarpaulin with mesh"><div class="band">Tarpaulin</div></div>
<div class="tile" style="left:75px;top:1309px;background:linear-gradient(135deg,#4f5a44,#8a8070 50%,#c86a2c 75%,#3a4436)" role="img" aria-label="Angler in an orange jacket by the water"><div class="band">Fishing</div></div>
<div class="tile" style="left:616px;top:1309px;background:linear-gradient(160deg,#3d4247,#8b9096 35%,#5f9a2e 70%,#4a8024)" role="img" aria-label="Golf bag on a trolley on grass"><div class="band">Golf</div></div>

<section class="products">
  <div class="products-title">
    <svg width="38" height="20" viewBox="0 0 38 20"><path d="M2 10h34M10 2L2 10l8 8" fill="none" stroke="#fff" stroke-width="4"/></svg>
    <span>Products</span>
    <svg width="38" height="20" viewBox="0 0 38 20"><path d="M2 10h34M28 2l8 8-8 8" fill="none" stroke="#fff" stroke-width="4"/></svg>
  </div>
  <div class="product-photo" role="img" aria-label="Towel holder clipped to a golf bag with a hand pulling the towel">
    <svg class="abs" style="left:12px;top:185px" width="20" height="34" viewBox="0 0 20 34"><path d="M17 2L3 17l14 15" fill="none" stroke="#fff" stroke-width="2.5"/></svg>
    <svg class="abs" style="left:478px;top:185px" width="20" height="34" viewBox="0 0 20 34"><path d="M3 2l14 15L3 32" fill="none" stroke="#fff" stroke-width="2.5"/></svg>
    <div class="thumb" role="img" aria-label="Grey towel hanging from the holder clip"></div>
  </div>
  <div class="product-info">
    <h3>4620 Golf Towel Holder</h3>
    <p>A towel holder with removable towel. With a clean club and golf ball, you will have a higher possibility to have better score. People say with clean equipment, the difference is the same as a birdie or a boogie. Golf professionals always clean their ball before the putt a ball on green. A traditional towel sitting in a eyelet on the golf bag it just not possible. You need at removable towel. A towel that is easy to remove and easy accessable + easy to pack. With Quibrel Outdoor towel holder, it's possible. If you have a favorite towel, it can also be used. The towel holder works with any normal microfiber, cotton or terry towel.</p>
  </div>
  <a class="btn btn-dark" href="#" style="left:617px;top:484px;width:179px;height:52px">Read More</a>
  <a class="btn btn-orange" href="#" style="left:816px;top:484px;width:179px;height:52px">Buy Now</a>
</section>

<h2 class="section-title about-title">About Quibrel Outdoor</h2>
<div class="about-photo" role="img" aria-label="Angler in an orange jacket holding a fly rod and net"></div>
<p class="about-text">Sed ut perspiciatis unde omnis iste natus error sit voluptatem accusantium doloremque laudantium, totam rem aperiam, eaque ipsa quae ab illo inventore veritatis et quasi architecto beatae vitae dicta sunt explicabo. Nemo enim ipsam voluptatem quia voluptas sit aspernatur aut odit aut fugit, sed quia consequuntur magni dolores eos qui ratione voluptatem sequi nesciunt.</p>
<a class="btn btn-orange" href="#" style="left:75px;top:2941px;width:179px;height:52px">Read More</a>

<h2 class="section-title news-title">Latest News</h2>
<article class="news-item" style="top:2460px">
  <div class="pic" role="img" aria-label="Fisherman at sunset by the water" style="background:linear-gradient(135deg,#c9b8a6,#8a7e74 50%,#3a3a40)"></div>
  <h4>Sed ut perspiciatis unde omnis iste natus</h4>
  <p>Accusantium doloremque laudantium, totam rem aperiam, eaque ipsa quae ab illo inventore veritatis et quasi architecto beatae vitae dicta sunt explicabo.</p>
</article>
<article class="news-item" style="top:2654px">
  <div class="pic" role="img" aria-label="Wooden boat panel with a green label" style="background:linear-gradient(135deg,#5a1f0c,#a8481e 50%,#3a1206)"></div>
  <h4>Sed ut perspiciatis unde omnis iste natus</h4>
  <p>Accusantium doloremque laudantium, totam rem aperiam, eaque ipsa quae ab illo inventore veritatis et quasi architecto beatae vitae dicta sunt explicabo.</p>
</article>
<article class="news-item" style="top:2848px">
  <div class="pic" role="img" aria-label="Towel hanging from a golf bag on grass" style="background:linear-gradient(135deg,#4e7a2a,#8a8f90 50%,#3e6a22)"></div>
  <h4>Sed ut perspiciatis unde omnis iste natus</h4>
  <p>Accusantium doloremque laudantium, totam rem aperiam, eaque ipsa quae ab illo inventore veritatis et quasi architecto beatae vitae dicta sunt explicabo.</p>
</article>

<footer class="site-footer">
  <div class="foot-brand"><span class="brand-dot"></span><span class="brand-name">Quibrel</span></div>
  <h3 class="foot-h" style="left:253px;top:34px">Subscribe Newsletter</h3>
  <div class="newsletter-input">Email Address</div>
  <a class="btn btn-orange signup" href="#">Sign Up</a>
  <h3 class="foot-h" style="left:884px;top:34px">Follow Us</h3>
  <div class="social"><span>Postvine</span><span>Chirrup</span><span>Snapfold</span><span>Workloop</span><span>Clipreel</span></div>
  <div class="divider"></div>
  <div class="foot-col" style="left:75px"><h5>Quick Links</h5><ul><li>Home</li><li>About Us</li><li>Categories</li><li>Products</li><li>Latest News</li><li>Contact Us</li></ul></div>
  <div class="foot-col" style="left:332px"><h5>Products</h5><ul><li>Neque porro quisquam</li><li>Est. qui dolorem</li><li>Lpsum quia dolor</li><li>Sit amet</li><li>Nemo enim ipsam</li></ul></div>
  <div class="foot-col" style="left:629px"><h5>Contact Us</h5><ul><li>Neque porro quisquam</li><li>Est. qui dolorem</li><li>1-800-555-0142</li><li>info@quibreloutdoor.com</li></ul></div>
  <div class="foot-col" style="left:885px"><h5>Shop By</h5><div class="shop-word">Tradovik</div></div>
</footer>
<div class="copyright">Copyright © 2021. Company Name. &nbsp;All Right Reserved</div>

</body>
</html>
```